Resposive web site in 4 languages + image gallery + logo design

We need a web page, which will work on all devices.
I have uploaded web page concept.
Company name: Praxelun
Industry/Entity Type
It Company
Logo Text
quality matters
Coding
Coded - Design and coding required
Number of Pages Required
1 page

```html
<!DOCTYPE html>
<html lang="en">
<head>
<meta charset="utf-8">
<title>Praxelun</title>
<link href="https://fonts.googleapis.com/css2?family=Questrial&family=Lato:ital,wght@0,400;0,700;1,400&display=swap" rel="stylesheet">
<style>
:root{
  --ink:#2b2b2b;
  --muted:#555;
  --white:#fff;
  --wood-dark:#2a180e;
  --wood-mid:#5a3620;
  --panel:#3d3d3d;
  --panel-deep:#2e2e2e;
  --footer:#323232;
  --bottom:#1d1d1d;
  --line:#666;
  --field:#fff;
}
*{box-sizing:border-box;margin:0;padding:0}
html,body{width:1200px;height:2329px;overflow:hidden}
body{position:relative;font-family:"Lato",sans-serif;color:var(--ink);background:var(--white)}
.abs{position:absolute}
.heading{font-family:"Questrial",sans-serif;font-weight:400}

/* header */
.site-header{position:absolute;left:0;top:0;width:1200px;height:86px;background:var(--white);border-top:2px solid #555}
.brand{position:absolute;left:132px;top:24px;font-family:"Questrial",sans-serif;font-size:34px;color:var(--ink);letter-spacing:1px;display:flex;align-items:center;gap:10px}
.brand-dot{width:12px;height:12px;background:var(--ink)}
.main-nav{position:absolute;top:44px;font-size:16px;color:var(--ink)}
.main-nav.active{border-bottom:2px solid var(--ink);padding-bottom:6px}
.lang-flag{position:absolute;left:905px;top:43px;width:44px;height:24px;background:linear-gradient(135deg,#1c3f8a,#c8102e 50%,#1c3f8a);border:1px solid #ccc}
.lang-caret{position:absolute;left:958px;top:50px}
.like-btn{position:absolute;left:998px;top:40px;width:70px;height:28px;background:#4a67ad;border:1px solid #3b5391;color:var(--white);font-weight:700;font-size:15px;line-height:26px;text-align:center;border-radius:2px}

/* hero */
.hero{position:absolute;left:0;top:86px;width:1200px;height:496px;background:linear-gradient(180deg,#2c3e5c 0%,#4a5468 30%,#6b5a48 60%,#2b2a22 100%)}
.hero-title{position:absolute;left:0;width:1200px;top:230px;text-align:center;font-size:38px;color:var(--white);font-family:"Lato",sans-serif;font-weight:700;text-shadow:0 2px 4px rgba(0,0,0,.5)}
.hero-btn{position:absolute;left:506px;top:288px;width:188px;height:51px;border:2px solid var(--white);color:var(--white);font-size:19px;font-weight:700;line-height:47px;text-align:center}
.hero-arrow{position:absolute;top:230px;width:44px;height:40px;background:rgba(255,255,255,.85);display:flex;align-items:center;justify-content:center}

/* section titles */
.section-title{position:absolute;left:0;width:1200px;text-align:center;font-family:"Questrial",sans-serif;font-size:34px}
.divider{position:absolute;left:283px;width:635px;height:2px}
.divider::before{content:"";position:absolute;left:0;right:0;top:0;height:1px;background:currentColor}
.divider::after{content:"";position:absolute;left:311px;top:-5px;width:11px;height:11px;border-radius:50%;background:currentColor}

/* welcome */
.welcome-text{position:absolute;left:150px;top:706px;width:900px;text-align:center;font-size:15.5px;line-height:25.5px;color:var(--ink)}
.outline-btn{position:absolute;left:532px;top:829px;width:134px;height:36px;border:1.5px solid var(--ink);font-size:15px;font-weight:700;line-height:33px;text-align:center}

/* services */
.services{position:absolute;left:0;top:913px;width:1200px;height:472px;background:linear-gradient(90deg,#1f1109 0%,#4d2e1a 25%,#5e3a22 50%,#4d2e1a 75%,#1f1109 100%);color:var(--white)}
.service-card{position:absolute;top:126px;width:296px;height:180px;background:var(--white);padding:9px}
.service-photo{width:100%;height:100%}
.service-name{position:absolute;top:324px;width:296px;text-align:center;font-weight:700;font-size:23px;letter-spacing:1px}
.service-text{position:absolute;top:370px;width:296px;text-align:center;font-size:15px;line-height:21px;padding:0 24px}

/* gallery */
.gallery-filter{position:absolute;top:1502px;font-size:15px;display:flex;align-items:center;gap:10px;color:var(--ink)}
.checkbox{width:15px;height:15px;border:1px solid #555;display:inline-block;position:relative}
.gallery-thumb{position:absolute;top:1550px;width:219px;height:143px;border:1px solid #999;padding:4px;background:var(--white)}
.gallery-thumb .fill{width:100%;height:100%}
.thumb-hover{box-shadow:0 4px 10px rgba(0,0,0,.4)}
.thumb-caption{position:absolute;left:4px;top:4px;right:4px;bottom:4px;background:rgba(40,40,40,.7);color:var(--white);text-align:center;padding-top:35px}
.thumb-caption b{display:block;font-size:16px;margin-bottom:8px}
.thumb-caption span{font-size:13px;line-height:19px;display:block;padding:0 20px}
.gallery-arrow{position:absolute;top:1607px}

/* contact band */
.contact-band{position:absolute;left:0;top:1742px;width:1200px;height:340px;background:linear-gradient(160deg,#444 0%,#3a3a3a 50%,#333 100%);color:var(--white)}
.band-heading{position:absolute;top:34px;font-family:"Questrial",sans-serif;font-size:20px;letter-spacing:.5px}
.dotted{position:absolute;top:72px;height:0;border-top:1px dotted #888}
.form-intro{position:absolute;left:132px;top:84px;font-size:13px}
.field{position:absolute;background:var(--field);color:#555;font-size:12px;padding:6px 8px}
.submit-btn{position:absolute;left:132px;top:273px;width:84px;height:32px;border:1.5px solid #ddd;font-size:12px;font-weight:700;text-align:center;line-height:29px}
.testimonial-bubble{position:absolute;left:629px;top:92px;width:439px;height:149px;background:var(--white);border-radius:8px;color:#444;font-style:italic;font-size:13px;line-height:22px;padding:16px 20px 0 56px}
.quote-mark{position:absolute;left:22px;top:8px;font-family:Georgia,serif;font-size:44px;color:#bbb;font-style:normal}
.avatar{position:absolute;left:655px;top:227px;width:78px;height:78px;border-radius:50%;background:linear-gradient(135deg,#c9a58a,#6b7f99);border:3px solid var(--white)}
.client-name{position:absolute;left:748px;top:266px;font-weight:700;font-size:14px}

/* footer */
.site-footer{position:absolute;left:0;top:2082px;width:1200px;height:210px;background:var(--footer);color:#eee}
.footer-heading{position:absolute;top:37px;font-family:"Questrial",sans-serif;font-size:19px}
.footer-rule{position:absolute;top:68px;height:0;border-top:1px solid #555}
.footer-sep{position:absolute;top:30px;width:1px;height:150px;background:#444}
.quick-link{position:absolute;left:132px;font-size:13px}
.quick-link::before{content:"›";margin-right:10px;color:#aaa}
.contact-item{position:absolute;left:345px;font-size:13px;line-height:17px;display:flex;gap:14px}
.contact-item svg{flex:none}
.map-fill{position:absolute;left:613px;top:78px;width:173px;height:89px;background:linear-gradient(135deg,#cfe0ef,#e8dfc8 50%,#b9d3ea);border:2px solid #eee}
.footer-brand{position:absolute;left:885px;top:98px;font-family:"Questrial",sans-serif;font-size:32px;color:#777;letter-spacing:1px}
.copyright{position:absolute;left:0;top:2292px;width:1200px;height:37px;background:var(--bottom);color:#ddd;font-size:12px;text-align:center;line-height:37px}
</style>
</head>
<body>

<header class="site-header">
  <div class="brand"><span class="brand-dot"></span>PRAXELUN</div>
  <span class="main-nav active" style="left:470px">HOME</span>
  <span class="main-nav" style="left:553px">SERVICES</span>
  <span class="main-nav" style="left:658px">ABOUT US</span>
  <span class="main-nav" style="left:772px">CONTACT US</span>
  <div class="lang-flag" role="img" aria-label="English language flag"></div>
  <svg class="lang-caret" width="12" height="8" viewBox="0 0 12 8"><path d="M0 0h12L6 8z" fill="#333"/></svg>
  <div class="like-btn">Like</div>
</header>

<section class="hero" role="img" aria-label="Stone house with timber roof lit at dusk">
  <div class="hero-arrow" style="left:0"><svg width="12" height="16" viewBox="0 0 12 16"><path d="M10 1L3 8l7 7" stroke="#333" stroke-width="3" fill="none"/></svg></div>
  <div class="hero-arrow" style="right:0"><svg width="12" height="16" viewBox="0 0 12 16"><path d="M2 1l7 7-7 7" stroke="#333" stroke-width="3" fill="none"/></svg></div>
  <h1 class="hero-title">Are you interested in an estimate?</h1>
  <div class="hero-btn">GET A QUOTE</div>
</section>

<section class="welcome">
  <h2 class="section-title" style="top:622px">Welcome to PRAXELUN</h2>
  <div class="divider" style="top:683px;color:#333"></div>
  <p class="welcome-text">Praxelun is a company whose business operations include making wooden products, restoration and building structures from natural stone. All of our products are made by craftsmen and specialists who have extensive experience and knowledge in their fields. The products we offer are always handmade and we take the requests and ideas of the specific client into account We always strive to achieve the best possible quality.</p>
  <div class="outline-btn">READ MORE</div>
</section>

<section class="services">
  <h2 class="section-title" style="top:34px;color:var(--white)">Featured Services</h2>
  <div class="divider" style="top:96px;color:#fff"></div>

  <div class="service-card" style="left:132px"><div class="service-photo" role="img" aria-label="Interior with wooden staircase and fireplace" style="background:linear-gradient(135deg,#d8c8b0,#8a4f2a 60%,#4a2a18)"></div></div>
  <div class="service-name" style="left:132px">WOODWORKS</div>
  <p class="service-text" style="left:132px">Timber is, in essence, a natural and warm material. Wood is also relatively durable and easy to work with... [+]</p>

  <div class="service-card" style="left:452px"><div class="service-photo" role="img" aria-label="Kitchen with stone column and marble counter" style="background:linear-gradient(135deg,#e8e6e0,#c8c0b2 50%,#9a8a78)"></div></div>
  <div class="service-name" style="left:452px">STONE WORKS</div>
  <p class="service-text" style="left:452px">The natural stone found in the ground has been used in construction for centuries because of its durability... [+]</p>

  <div class="service-card" style="left:772px"><div class="service-photo" role="img" aria-label="Workers restoring a timber house facade" style="background:linear-gradient(90deg,#c07a48,#a85e32 60%,#6e9a4a)"></div></div>
  <div class="service-name" style="left:772px">RESTORATION</div>
  <p class="service-text" style="left:772px">It's good to see that fixing old things has become popular again in recent years and people... [+]</p>
</section>

<section class="gallery">
  <h2 class="section-title" style="top:1422px">Projects Gallery</h2>
  <div class="divider" style="top:1478px;color:#333"></div>

  <label class="gallery-filter" style="left:344px"><span class="checkbox"><svg width="13" height="13" viewBox="0 0 13 13" style="position:absolute;left:0;top:0"><path d="M2 7l3 3 6-8" stroke="#333" stroke-width="2" fill="none"/></svg></span>All</label>
  <label class="gallery-filter" style="left:448px"><span class="checkbox"></span>Woodworks</label>
  <label class="gallery-filter" style="left:604px"><span class="checkbox"></span>Stone Works</label>
  <label class="gallery-filter" style="left:750px"><span class="checkbox"></span>Restoration</label>

  <svg class="gallery-arrow" style="left:88px" width="14" height="24" viewBox="0 0 14 24"><path d="M12 2L3 12l9 10" stroke="#111" stroke-width="2.5" fill="none"/></svg>
  <svg class="gallery-arrow" style="left:1098px" width="14" height="24" viewBox="0 0 14 24"><path d="M2 2l9 10-9 10" stroke="#111" stroke-width="2.5" fill="none"/></svg>

  <div class="gallery-thumb" style="left:132px"><div class="fill" role="img" aria-label="Living room at night" style="background:linear-gradient(135deg,#2a2a30,#6a5a48 60%,#3a3028)"></div></div>
  <div class="gallery-thumb thumb-hover" style="left:371px">
    <div class="fill" role="img" aria-label="Interior renovation in progress" style="background:linear-gradient(135deg,#8a8a88,#5a5a58)"></div>
    <div class="thumb-caption"><b>Lorem ipsum dolor</b><span>Lorem ipsum dolor sit amet consectetur adipiscing elit.</span></div>
  </div>
  <div class="gallery-thumb" style="left:610px"><div class="fill" role="img" aria-label="Dark wooden kitchen with pendant lights" style="background:linear-gradient(135deg,#3a2a22,#7a6a5a 50%,#2a2018)"></div></div>
  <div class="gallery-thumb" style="left:849px"><div class="fill" role="img" aria-label="Chandelier in a purple room" style="background:linear-gradient(135deg,#5a4a8a,#b88a6a 55%,#3a2e5a)"></div></div>
</section>

<section class="contact-band">
  <h3 class="band-heading" style="left:132px">GET IN TOUCH WITH US</h3>
  <div class="dotted" style="left:132px;width:436px"></div>
  <p class="form-intro">Lorem ipsum dolor sit amet consectetur adipiscing sed dmmy nibh</p>
  <div class="field" style="left:132px;top:120px;width:206px;height:27px">First Name</div>
  <div class="field" style="left:359px;top:120px;width:209px;height:27px">Last Name</div>
  <div class="field" style="left:132px;top:157px;width:206px;height:28px">Email</div>
  <div class="field" style="left:359px;top:157px;width:209px;height:28px">Phone</div>
  <div class="field" style="left:132px;top:194px;width:436px;height:65px">Your Message</div>
  <div class="submit-btn">SUBMIT</div>

  <h3 class="band-heading" style="left:629px">CLIENT TESTIMONIALS</h3>
  <svg class="abs" style="left:1038px;top:40px" width="32" height="14" viewBox="0 0 32 14"><path d="M8 1L2 7l6 6M24 1l6 6-6 6" stroke="#ccc" stroke-width="1.5" fill="none"/></svg>
  <div class="dotted" style="left:629px;width:439px"></div>
  <div class="testimonial-bubble">
    <span class="quote-mark">&ldquo;</span>
    Lorem ipsum dolor sit amet consetug e sed diay nibh euismodl tincidunt ut laoreet dolore magam er vol wisi enim ad minim veniam quis nostrud exerci tationorem ipsum dolor sit ametee sed diammmy nibh euismd tincidunt ut laoreet dolore magna aliqur volpatl tiidunt ut laoreet dolore magna aliqur volpatl
  </div>
  <svg class="abs" style="left:868px;top:240px" width="82" height="36" viewBox="0 0 82 36"><path d="M0 0h82L78 36z" fill="#fff"/></svg>
  <div class="avatar" role="img" aria-label="Client portrait"></div>
  <div class="client-name">Mr. Elias Marrow</div>
</section>

<footer class="site-footer">
  <h4 class="footer-heading" style="left:132px">Quick Links</h4>
  <div class="footer-rule" style="left:132px;width:105px"></div>
  <a class="quick-link" style="top:77px">Home</a>
  <a class="quick-link" style="top:104px">Services</a>
  <a class="quick-link" style="top:130px">About Us</a>
  <a class="quick-link" style="top:157px">Contact Us</a>
  <div class="footer-sep" style="left:295px"></div>

  <h4 class="footer-heading" style="left:345px">Contact Information</h4>
  <div class="footer-rule" style="left:345px;width:175px"></div>
  <div class="contact-item" style="top:73px"><svg width="12" height="16" viewBox="0 0 12 16"><path d="M6 0a6 6 0 0 0-6 6c0 4.5 6 10 6 10s6-5.5 6-10a6 6 0 0 0-6-6zm0 8.5a2.5 2.5 0 1 1 0-5 2.5 2.5 0 0 1 0 5z" fill="#eee"/></svg><span>Varel 12 10115 Korvina<br>NORDLAND</span></div>
  <div class="contact-item" style="top:133px"><svg width="14" height="14" viewBox="0 0 14 14"><path d="M3 0l2.5 3.5-1.5 2a8 8 0 0 0 4.5 4.5l2-1.5L14 11l-1.5 2.5C6 14 0 8 .5 1.5z" fill="#eee"/></svg><span>014-552-9083</span></div>
  <div class="contact-item" style="top:155px"><svg width="14" height="11" viewBox="0 0 14 11"><path d="M0 0h14v11H0z" fill="#eee"/><path d="M0 0l7 6 7-6" stroke="#323232" stroke-width="1.2" fill="none"/></svg><span>sales@praxelun.com</span></div>
  <div class="footer-sep" style="left:590px"></div>

  <h4 class="footer-heading" style="left:613px">Location Map</h4>
  <div class="footer-rule" style="left:613px;width:175px"></div>
  <div class="map-fill" role="img" aria-label="Street map showing office location"></div>
  <div class="footer-sep" style="left:834px"></div>

  <div class="footer-brand">PRAXELUN</div>
</footer>
<div class="copyright">Copyright © 2016 PRAXELUN.  All Rights Reserved.</div>

</body>
</html>
```